Oil and Gas Exploration and Production company needs a business card design

We need a business card design using our logo and colors in the logo. We want a mainstream design.

```html
<!DOCTYPE html>
<html lang="en">
<head>
<meta charset="utf-8">
<title>Kestrel Oil &amp; Gas – Business Card</title>
<link href="https://fonts.googleapis.com/css2?family=Work+Sans:wght@400;500;600;700&display=swap" rel="stylesheet">
<style>
  :root {
    --page-bg: #e6e9ee;
    --card-black: #0e0e0f;
    --card-sheen: #3a3a3c;
    --gold: #c8943a;
    --gold-soft: #b8893a;
    --white: #f4f4f2;
    --address: #a3abbd;
    --contact: #d9cdbf;
  }
  * { box-sizing: border-box; margin: 0; padding: 0; }
  html, body {
    width: 1200px; height: 900px; overflow: hidden;
    background: var(--page-bg);
    font-family: "Work Sans", Arial, sans-serif;
  }
  .business-card {
    position: absolute; left: 150px; top: 195px;
    width: 900px; height: 510px;
    background:
      radial-gradient(ellipse 60% 90% at 40% 45%, rgba(80,80,84,0.55), transparent 70%),
      linear-gradient(100deg, var(--card-sheen) 0%, #1c1c1e 35%, var(--card-black) 70%, #1a1a1b 100%);
    box-shadow: 0 14px 40px rgba(0,0,0,0.25);
    color: var(--white);
  }
  .brand {
    position: absolute; left: 44px; top: 52px;
    display: flex; align-items: center; gap: 14px;
  }
  .brand-dot {
    width: 26px; height: 26px; border-radius: 50%;
    background: var(--white);
  }
  .brand-name {
    font-weight: 700; font-size: 44px; letter-spacing: -0.5px;
    color: var(--white); line-height: 1;
  }
  .holder { position: absolute; left: 42px; top: 226px; }
  .holder-name {
    font-size: 38px; font-weight: 500; color: var(--gold); line-height: 1.1;
  }
  .holder-title {
    font-size: 19px; color: #d6d6d6; margin-top: 4px; letter-spacing: 0.5px;
  }
  .address {
    position: absolute; left: 42px; top: 312px;
    font-size: 20px; line-height: 1.45; color: var(--address);
  }
  .contacts {
    position: absolute; left: 42px; top: 385px;
    list-style: none; font-size: 20px; color: var(--contact);
  }
  .contacts li { display: flex; align-items: center; gap: 12px; height: 29px; }
  .contacts svg { width: 15px; height: 15px; flex: none; }
  .emblem-area {
    position: absolute; left: 435px; top: 45px;
    width: 420px; height: 420px;
  }
</style>
</head>
<body>
  <main class="business-card">
    <div class="brand">
      <span class="brand-dot"></span>
      <span class="brand-name">Kestrel Oil &amp; Gas</span>
    </div>

    <div class="holder">
      <p class="holder-name">Dale Whitaker</p>
      <p class="holder-title">CFO</p>
    </div>

    <p class="address">4820 Cedar Ridge Rd,<br>Midland, Texas US</p>

    <ul class="contacts">
      <li>
        <svg viewBox="0 0 16 16" fill="none" stroke="#c8943a" stroke-width="1.6" stroke-linecap="round" stroke-linejoin="round"><path d="M4 1.5 6 5 4.6 6.4a9 9 0 0 0 5 5L11 10l3.5 2-1 2.5C7 14.5 1.5 9 1.5 2.5Z"/></svg>
        <span>(555) 014-2290</span>
      </li>
      <li>
        <svg viewBox="0 0 16 16" fill="none" stroke="#c8943a" stroke-width="1.5" stroke-linejoin="round"><rect x="1.5" y="3.5" width="13" height="9" rx="1"/><path d="m1.5 4 6.5 5 6.5-5"/></svg>
        <span>info@kestreloilgas.com</span>
      </li>
      <li>
        <svg viewBox="0 0 16 16" fill="none" stroke="#c8943a" stroke-width="1.4"><circle cx="8" cy="8" r="6.5"/><path d="M1.5 8h13M8 1.5c3 3.5 3 9.5 0 13M8 1.5c-3 3.5-3 9.5 0 13"/></svg>
        <span>www.kestreloilgas.com</span>
      </li>
    </ul>

    <svg class="emblem-area" viewBox="0 0 420 420" role="img" aria-label="Space for the large company emblem in gold">
      <defs>
        <radialGradient id="emblemGlow" cx="50%" cy="50%" r="50%">
          <stop offset="0%" stop-color="#c8943a" stop-opacity="0.35"/>
          <stop offset="100%" stop-color="#c8943a" stop-opacity="0"/>
        </radialGradient>
      </defs>
      <circle cx="210" cy="210" r="200" fill="url(#emblemGlow)"/>
    </svg>
  </main>
</body>
</html>
```